Business Card for Multi-Brand Sportswear Company

We are looking for a business card which represents our company and the multiple brands within it.

The company: Fen Athletics (LTD)
The brands: Fen, TavaPuni, ElmStretch, Grit and Rain

Employees using these cards would be representing Fen Athletics, rather than any of the individual brands. You will see a current design within the uploaded files, to give some inspiration. The actual text of the brands is not necessary, but the logos should be on there is some format.

Our creative minds on this are stretched, so we are looking for someone to make this their own, and show us what a good business card should look like.

We may like to get these printed with spot gloss, so keep that in mind with your designs.

www.fenathletics.co.uk

Industry/Entity Type

Business

Contact Information for Business Card

Leo Pemberton-Hale
Operations Manager
(+44) 1632 960 418
Leo@fenathletics.co.uk
www.fenathletics.co.uk

Font styles to use
Sans Serif
Other font styles liked:
• Eurostile

Colors
ffffff

Requirements
Nice to have
• Dark (black) background

```html
<!DOCTYPE html>
<html lang="en">
<head>
<meta charset="utf-8">
<title>Fen Athletics – Business Card</title>
<link rel="stylesheet" href="https://fonts.googleapis.com/css2?family=Saira:wght@400;500;600;700&display=swap">
<style>
  :root {
    --backdrop: #3b3b3b;
    --card: #ffffff;
    --ink: #111111;
    --text: #2b2b2b;
    --muted: #5a5a5a;
    --accent: #e5212d;
    --brand-grey: #8c8c8c;
    --brand-plum: #6a5670;
  }
  * { box-sizing: border-box; margin: 0; padding: 0; }
  html, body { width: 1105px; height: 1200px; overflow: hidden; }
  body {
    background: var(--backdrop);
    font-family: "Saira", "Helvetica Neue", Arial, sans-serif;
    color: var(--text);
    position: relative;
  }
  .card {
    position: absolute;
    left: 196px;
    width: 720px;
    height: 412px;
    background: var(--card);
    overflow: hidden;
  }
  .card--front { top: 146px; }
  .card--back { top: 602px; height: 410px; }

  .wordmark { position: absolute; text-align: left; color: var(--ink); }
  .wordmark__name {
    display: block;
    font-weight: 600;
    line-height: 1;
    letter-spacing: 0.5px;
    color: var(--ink);
  }
  .wordmark__tagline {
    display: block;
    font-weight: 400;
    letter-spacing: 2.5px;
    color: var(--muted);
    text-transform: uppercase;
  }
  .card--front .wordmark { right: 39px; top: 56px; text-align: right; }
  .card--front .wordmark__name { font-size: 46px; }
  .card--front .wordmark__tagline { font-size: 12px; margin-top: 8px; }
  .card--back .wordmark { left: 0; right: 0; top: 130px; text-align: center; }
  .card--back .wordmark__name { font-size: 64px; }
  .card--back .wordmark__tagline { font-size: 15px; margin-top: 10px; letter-spacing: 3.5px; }

  .person { position: absolute; left: 40px; top: 224px; }
  .person__name { font-size: 26px; font-weight: 600; color: var(--accent); line-height: 1.1; }
  .person__role { font-size: 19px; font-weight: 400; color: var(--ink); margin-top: 4px; }

  .divider {
    position: absolute; left: 40px; right: 39px; top: 288px;
    height: 1.5px; background: var(--ink);
  }
  .contact { position: absolute; left: 40px; top: 298px; list-style: none; }
  .contact__item {
    display: flex; align-items: center; gap: 10px;
    font-size: 18px; color: var(--muted); height: 28px;
  }
  .contact__icon { width: 16px; height: 16px; fill: var(--accent); flex: none; }
  .address {
    position: absolute; right: 39px; top: 298px;
    font-style: normal; text-align: right;
    font-size: 18px; line-height: 28px; color: var(--muted);
  }
  .footer-band { position: absolute; left: 0; bottom: 0; width: 720px; height: 56px; }
  .website {
    position: absolute; right: 39px; bottom: 9px;
    font-size: 17px; font-weight: 500; letter-spacing: 2px; color: var(--card);
  }

  .brand-row {
    position: absolute; left: 0; right: 0; top: 340px;
    display: flex; list-style: none;
  }
  .brand-row__item {
    position: absolute; transform: translateX(-50%);
    display: flex; align-items: center; gap: 7px;
    font-size: 19px; font-weight: 600; white-space: nowrap;
  }
  .brand-row__item--tava { left: 84px; color: var(--brand-grey); }
  .brand-row__item--elm { left: 257px; color: var(--brand-plum); }
  .brand-row__item--grit { left: 429px; color: var(--accent); }
  .brand-row__item--fen { left: 602px; color: var(--ink); }
  .brand-row__dot { width: 14px; height: 14px; border-radius: 50%; border: 2px solid currentColor; }
  .brand-row__square { width: 14px; height: 14px; background: currentColor; }
</style>
</head>
<body>

<section class="card card--front" aria-label="Business card front">
  <div class="wordmark">
    <span class="wordmark__name">Fen Athletics</span>
    <span class="wordmark__tagline">Performance Wear</span>
  </div>

  <div class="person">
    <p class="person__name">Owen Thackeray</p>
    <p class="person__role">Managing Director</p>
  </div>

  <div class="divider"></div>

  <ul class="contact">
    <li class="contact__item">
      <svg class="contact__icon" viewBox="0 0 24 24" aria-hidden="true"><path d="M6.6 10.8a15.1 15.1 0 0 0 6.6 6.6l2.2-2.2c.3-.3.7-.4 1-.2 1.1.4 2.3.6 3.6.6.6 0 1 .4 1 1V20c0 .6-.4 1-1 1A17 17 0 0 1 3 4c0-.6.4-1 1-1h3.5c.6 0 1 .4 1 1 0 1.3.2 2.5.6 3.6.1.3 0 .7-.2 1z"/></svg>
      <span>+44 (0)1632 960418</span>
    </li>
    <li class="contact__item">
      <svg class="contact__icon" viewBox="0 0 24 24" aria-hidden="true"><path d="M2 5h20v14H2z M2 5l10 8 10-8" fill="var(--accent)"/><path d="M3 6l9 7 9-7" fill="none" stroke="#fff" stroke-width="1.8"/></svg>
      <span>owen@fenathletics.co.uk</span>
    </li>
  </ul>

  <address class="address">
    Heron Yard, Ashby Fold<br>
    Linton, LN4 2QX
  </address>

  <svg class="footer-band" viewBox="0 0 720 56" aria-hidden="true">
    <rect x="0" y="26" width="380" height="30" fill="var(--ink)"/>
    <path d="M367 56 C 385 40 398 2 440 2 H720 V56 Z" fill="var(--accent)"/>
  </svg>
  <span class="website">www.fenathletics.co.uk</span>
</section>

<section class="card card--back" aria-label="Business card back">
  <div class="wordmark">
    <span class="wordmark__name">Fen Athletics</span>
    <span class="wordmark__tagline">Performance Wear</span>
  </div>

  <ul class="brand-row" aria-label="Group brands">
    <li class="brand-row__item brand-row__item--tava"><span class="brand-row__dot"></span>TavaPuni</li>
    <li class="brand-row__item brand-row__item--elm"><span class="brand-row__square"></span>ElmStretch</li>
    <li class="brand-row__item brand-row__item--grit">Grit and Rain</li>
    <li class="brand-row__item brand-row__item--fen">Fen</li>
  </ul>
</section>

</body>
</html>
```